Website for software company "velora"

We need a website for our software company/startup named "velora". We are developing several products (currently 3 standard-software products) which are all in different sectors, but all our products are available for Laptops/PC/Mobile Phones/Tablets, ... We do also create custom software and support our customers with consulting to optimize their processes.
We already have a Logo which you can find in the attached files.
We are a young team of 4 members (two founders and 2 employees).

To get an idea of our products -> the first one is a planning software for healthcare organizations (eg. BlueHaven, firebrigade, pharmacy), the second one is a booking software for sport clubs and the third one is a competition software for sports hunting. You see very diverse. Include or ignore this info of our products as you like.

The design has to be a bootstrap 4 (or higher) design. We have licenced FontAwesome as iconset. Responsive design should come without saying.

• Starting page, product pages, news section, contact, team, services

```html
<!DOCTYPE html>
<html lang="en">
<head>
<meta charset="utf-8">
<title>velora — Software for every sector</title>
<link rel="stylesheet" href="https://fonts.googleapis.com/css2?family=Roboto+Condensed:wght@400;700&family=Lato:wght@400;700&display=swap">
<style>
:root{
  --orange:#f4792b;
  --orange-light:#f89a4e;
  --navy:#1f2633;
  --footer:#161b26;
  --text:#333a44;
  --line:#dcdfe4;
  --white:#ffffff;
}
*{box-sizing:border-box;margin:0;padding:0}
html,body{width:1200px;height:4118px;overflow:hidden}
body{position:relative;background:var(--white);font-family:'Lato',sans-serif;color:var(--text)}
.abs{position:absolute}

/* brand */
.brand{font-family:'Roboto Condensed',sans-serif;font-weight:700;letter-spacing:2px;display:flex;align-items:center;gap:10px}
.brand-mark{width:14px;height:14px;background:var(--orange)}

/* header */
.topbar{left:0;top:0;width:1200px;height:64px;background:var(--white)}
.topbar .brand{position:absolute;left:112px;top:12px;font-size:42px;color:var(--navy)}
.contact-pill{position:absolute;top:18px;display:flex;align-items:center;gap:12px;font-size:13.5px;color:var(--navy)}
.contact-pill .ico{width:30px;height:30px;border-radius:50%;background:var(--orange);display:flex;align-items:center;justify-content:center}
.contact-pill b{font-weight:400;color:var(--orange)}
.demo-btn{position:absolute;left:952px;top:11px;width:136px;height:42px;border:2px solid var(--orange);color:var(--orange);font:700 14px 'Roboto Condensed',sans-serif;display:flex;align-items:center;justify-content:center;gap:8px;border-radius:2px}
.mainnav{left:472px;top:64px;width:728px;height:42px;background:var(--orange);clip-path:polygon(28px 0,100% 0,100% 100%,0 100%);z-index:3}
.mainnav a{position:absolute;top:12px;color:var(--white);font:700 14.5px 'Roboto Condensed',sans-serif;text-decoration:none}

/* button arrow */
.go{width:13px;height:13px;border-radius:50%;background:var(--white);display:inline-block;position:relative}
.go::after{content:"";position:absolute;left:5px;top:3.5px;border-left:4px solid var(--orange);border-top:3px solid transparent;border-bottom:3px solid transparent}
.demo-btn .go{background:var(--orange)}
.demo-btn .go::after{border-left-color:var(--white)}
.btn{position:absolute;height:50px;background:var(--orange);color:var(--white);font:700 14.5px 'Roboto Condensed',sans-serif;display:flex;align-items:center;justify-content:center;gap:10px;border-radius:3px;box-shadow:0 4px 10px rgba(244,121,43,.3)}
.btn.dark{background:var(--navy);box-shadow:none}
.btn.dark .go::after{border-left-color:var(--navy)}

/* hero */
.hero-photo{left:0;top:64px;width:1200px;height:648px;background:linear-gradient(100deg,#cfd3d6 0%,#e6e4df 35%,#d8c3ac 55%,#ecebe8 75%,#d9dadc 100%)}
.welcome{left:112px;top:219px;width:403px;height:293px;background:rgba(90,90,95,.72)}
.welcome .kicker{position:absolute;left:77px;top:27px;color:var(--white);font:700 29px 'Roboto Condensed',sans-serif}
.marker{position:relative}
.marker::before{content:"";position:absolute;left:-30px;top:5px;border-left:16px solid var(--orange);border-top:11px solid transparent;border-bottom:11px solid transparent}
.welcome h1{position:absolute;left:42px;top:60px;color:var(--white);font:700 72px 'Roboto Condensed',sans-serif;letter-spacing:1px}
.welcome p{position:absolute;left:44px;top:148px;width:330px;color:var(--white);font-size:14px;line-height:26px}
.social-rail{left:1114px;top:208px;width:32px}
.ring{width:32px;height:32px;border:1.5px solid var(--navy);border-radius:50%;margin-bottom:11px;display:flex;align-items:center;justify-content:center}
.chev{position:absolute;width:10px;height:10px;border-left:1.5px solid var(--navy);border-top:1.5px solid var(--navy)}

/* sections */
.section-title{position:absolute;left:0;width:1200px;text-align:center;font:700 35px 'Roboto Condensed',sans-serif;color:var(--navy)}
.section-title .marker::before{left:-28px;top:8px}
.item-title{position:absolute;font:700 29px 'Roboto Condensed',sans-serif;color:var(--navy)}
.item-title .marker::before{left:-26px;top:5px;border-left-width:14px;border-top-width:12px;border-bottom-width:12px}
.copy{position:absolute;width:440px;font-size:14.5px;line-height:25.6px;text-align:justify;color:var(--text)}
.shot{position:absolute;width:392px;height:325px;border-radius:44px 0 44px 0}
.shot-frame{position:absolute;width:392px;height:325px;border-top:3px solid #e4e6ea;border-left:3px solid #e4e6ea;border-radius:44px 0 0 0}
.shot-frame::after{content:"";position:absolute;left:8px;top:8px;right:-8px;bottom:0;border-top:1.5px solid var(--orange);border-left:1.5px solid var(--orange);border-radius:38px 0 0 0}

/* about */
.about-band{left:0;top:2125px;width:1200px;height:510px;background:linear-gradient(90deg,#a7a29b 0%,#c9b8a6 30%,#d98b52 48%,var(--orange) 62%,var(--orange-light) 100%)}
.about-title{left:673px;top:2184px;color:var(--white)}
.about-title .marker::before{border-left-color:var(--white)}
.about-copy{left:642px;top:2238px;width:444px;color:var(--white)}

/* news */
.card{position:absolute;top:2782px;width:309px;height:420px;border:1.5px solid var(--line);background:var(--white);text-align:center}
.card .thumb{position:absolute;left:9px;top:9px;width:289px;height:202px}
.date{position:absolute;left:98px;top:211px;width:113px;height:32px;background:var(--orange);color:var(--white);font:700 14px 'Roboto Condensed',sans-serif;line-height:32px;border-radius:3px}
.card h3{position:absolute;left:20px;top:258px;width:267px;font:700 14.5px 'Roboto Condensed',sans-serif;line-height:21px;color:var(--navy);text-transform:uppercase}
.card p{position:absolute;left:30px;top:302px;width:248px;font-size:14px;line-height:25.6px;color:var(--text);text-align:justify;text-align-last:center}
.card .more{position:absolute;left:0;top:384px;width:100%;display:flex;justify-content:center;align-items:center;gap:10px;color:var(--orange);font:700 14px 'Roboto Condensed',sans-serif;text-decoration:underline}
.card .more .go{background:var(--orange)}
.card .more .go::after{border-left-color:var(--white)}

/* contact */
.contact-left{left:0;top:3288px;width:600px;height:539px;background:linear-gradient(120deg,#ee7a34 0%,var(--orange) 50%,#f38a44 100%)}
.contact-right{left:600px;top:3288px;width:600px;height:539px;background:linear-gradient(100deg,#f2f2f3 0%,#e9e9ec 50%,#f3f3f5 100%)}
.contact-title{left:154px;top:3392px;color:var(--white);font:700 33px 'Roboto Condensed',sans-serif}
.contact-row{position:absolute;left:128px;display:flex;align-items:center;gap:16px;color:var(--white);font-size:21px;line-height:30px}
.contact-row .ico{width:44px;height:44px;border:2px solid var(--white);border-radius:50%;display:flex;align-items:center;justify-content:center;flex:none}
.touch-title{left:716px;top:3366px}
.field{position:absolute;height:45px;background:var(--white);border:1px solid var(--line);display:flex;align-items:center;gap:12px;padding-left:20px;font-size:14px;color:#3a3f48}
.field.tall{height:112px;align-items:flex-start;padding-top:14px}
.submit{left:686px;top:3694px;width:148px;font-size:17px}

/* footer */
.footer{left:0;top:3827px;width:1200px;height:291px;background:var(--footer)}
.footer .brand{position:absolute;left:0;width:1200px;justify-content:center;top:52px;font-size:44px;color:var(--white)}
.foot-nav{position:absolute;left:0;top:124px;width:1200px;display:flex;justify-content:center;gap:30px;color:var(--white);font-size:15px}
.foot-social{position:absolute;left:0;top:177px;width:1200px;display:flex;justify-content:center;gap:8px}
.foot-social span{width:30px;height:30px;border-radius:50%;background:var(--orange);display:flex;align-items:center;justify-content:center}
.foot-rule{position:absolute;left:112px;top:241px;width:977px;height:1px;background:#4a505c}
.copyright{position:absolute;left:0;top:262px;width:1200px;text-align:center;color:var(--white);font-size:12.5px}
</style>
</head>
<body>

<!-- HERO -->
<div class="abs hero-photo" role="img" aria-label="Smiling woman working on a laptop at a bright white office desk"></div>
<svg class="abs" style="left:0;top:590px" width="1200" height="122" viewBox="0 0 1200 122">
  <polygon points="0,38 320,114 876,114 1200,38 1200,122 0,122" fill="#ffffff"/>
  <polyline points="0,10 600,64 1200,10" fill="none" stroke="#c9cbd0" stroke-width="1.5" opacity=".7"/>
  <polyline points="0,36 320,110 876,110 1200,36" fill="none" stroke="#f4792b" stroke-width="6"/>
  <polyline points="0,46 320,118 876,118 1200,46" fill="none" stroke="#f4792b" stroke-width="1.5"/>
</svg>

<header>
  <div class="abs topbar">
    <div class="brand"><span class="brand-mark"></span>VELORA</div>
    <div class="contact-pill" style="left:488px"><span class="ico">
      <svg width="14" height="14" viewBox="0 0 24 24"><path fill="#fff" d="M6.6 10.8a15 15 0 0 0 6.6 6.6l2.2-2.2a1 1 0 0 1 1-.25 11.4 11.4 0 0 0 3.6.57 1 1 0 0 1 1 1V20a1 1 0 0 1-1 1A17 17 0 0 1 3 4a1 1 0 0 1 1-1h3.5a1 1 0 0 1 1 1c0 1.25.2 2.45.57 3.57a1 1 0 0 1-.25 1z"/></svg></span>
      <span><b>Call Us:</b> +1 555 014 2200</span></div>
    <div class="contact-pill" style="left:727px"><span class="ico">
      <svg width="14" height="14" viewBox="0 0 24 24"><path fill="#fff" d="M2 5h20v14H2z"/><path d="M2 5l10 8 10-8" fill="none" stroke="#f4792b" stroke-width="2"/></svg></span>
      <span><b>Email:</b> +1 555 014 2200</span></div>
    <div class="demo-btn">GET A DEMO <span class="go"></span></div>
  </div>
  <nav class="abs mainnav">
    <a style="left:72px">HOME</a>
    <a style="left:150px">ABOUT US</a>
    <a style="left:252px">OUR SOFTWARE</a>
    <a style="left:392px">OUR NEWS</a>
    <a style="left:499px">CONTACT US</a>
  </nav>
</header>

<section class="abs welcome">
  <div class="kicker"><span class="marker"></span>WELCOME TO</div>
  <h1>VELORA</h1>
  <p>Lorem ipsum dolor sited consectetur eiusmod tempor incididunt ut labore et dolore magna.</p>
  <div class="btn" style="left:43px;top:213px;width:154px;height:48px">GET STARTED <span class="go"></span></div>
</section>

<div class="abs social-rail" aria-label="Social links">
  <div class="ring"><svg width="14" height="14" viewBox="0 0 24 24"><circle cx="12" cy="12" r="9" fill="none" stroke="#1f2633" stroke-width="2"/><path d="M3 12h18M12 3c4 4 4 14 0 18M12 3c-4 4-4 14 0 18" fill="none" stroke="#1f2633" stroke-width="1.6"/></svg></div>
  <div class="ring"><svg width="14" height="14" viewBox="0 0 24 24"><path d="M3 4h18v12H9l-5 4v-4H3z" fill="#1f2633"/></svg></div>
  <div class="ring"><svg width="14" height="14" viewBox="0 0 24 24"><circle cx="18" cy="5" r="3" fill="#1f2633"/><circle cx="6" cy="12" r="3" fill="#1f2633"/><circle cx="18" cy="19" r="3" fill="#1f2633"/><path d="M18 5L6 12l12 7" fill="none" stroke="#1f2633" stroke-width="2"/></svg></div>
  <span class="chev" style="left:11px;top:137px;transform:rotate(45deg)"></span>
  <span class="abs" style="left:8px;top:154px;width:16px;height:16px;border:1.5px solid var(--navy);border-radius:50%"></span>
  <span class="abs" style="left:13px;top:159px;width:6px;height:6px;background:var(--navy);border-radius:50%"></span>
  <span class="abs" style="left:13px;top:181px;width:5px;height:5px;background:var(--navy);border-radius:50%"></span>
  <span class="abs" style="left:13px;top:199px;width:5px;height:5px;background:var(--navy);border-radius:50%"></span>
  <span class="abs" style="left:15px;top:214px;width:1px;height:56px;background:var(--navy)"></span>
  <span class="chev" style="left:11px;top:278px;transform:rotate(225deg)"></span>
</div>

<!-- OUR SOFTWARE -->
<h2 class="section-title" style="top:770px"><span class="marker">OUR SOFTWARE</span></h2>

<h3 class="item-title" style="left:157px;top:887px"><span class="marker">HEALTHCARE ORGANIZATIONS</span></h3>
<p class="copy" style="left:131px;top:941px">Lorem ipsum dolor sit amet, consectetur adipiscing elit, sed do eiusmod tempor incididunt ut labore et dolore magna aliqua.set enim ad minim veniam, quis nostrud exercitation ullamco laboris nisi ut aliquip ex ea commodo consequat. Duis aute irure dolor in reprehenderit in voluptate velit esse cillum dolore eu fugiat nulla pariatur. Excepteur sint occaecat cupidatat non proident, sunt in culpa qui officia deserunt mollit anim id est laborum.Lorem ipsum dolor sit amet, consectetur adipiscing occaecat cupidatat.</p>
<div class="btn" style="left:131px;top:1171px;width:153px">LEARN MORE <span class="go"></span></div>
<div class="shot-frame" style="left:656px;top:885px"></div>
<div class="shot" style="left:677px;top:906px;background:linear-gradient(135deg,#b9c3cc 0%,#e4e6e8 40%,#7d6b60 70%,#c7ccd2 100%)" role="img" aria-label="Medical staff in white coats reviewing documents at a meeting table"></div>

<div class="shot-frame" style="left:144px;top:1288px"></div>
<div class="shot" style="left:165px;top:1309px;background:linear-gradient(180deg,#dfe5ea 0%,#8fa3b5 35%,#7fa54f 60%,#5f8c35 100%)" role="img" aria-label="Young football player in blue kit kicking a ball on a training pitch"></div>
<h3 class="item-title" style="left:645px;top:1290px"><span class="marker">SPORT CLUBS</span></h3>
<p class="copy" style="left:619px;top:1344px">Lorem ipsum dolor sit amet, consectetur adipiscing elit, sed do eiusmod tempor incididunt ut labore et dolore magna aliqua.set enim ad minim veniam, quis nostrud exercitation ullamco laboris nisi ut aliquip ex ea commodo consequat. Duis aute irure dolor in reprehenderit in voluptate velit esse cillum dolore eu fugiat nulla pariatur. Excepteur sint occaecat cupidatat non proident, sunt in culpa qui officia deserunt mollit anim id est laborum.Lorem ipsum dolor sit amet, consectetur adipiscing occaecat cupidatat.</p>
<div class="btn" style="left:619px;top:1574px;width:153px">LEARN MORE <span class="go"></span></div>

<h3 class="item-title" style="left:157px;top:1692px"><span class="marker">SPORTS HUNTING</span></h3>
<p class="copy" style="left:131px;top:1746px">Lorem ipsum dolor sit amet, consectetur adipiscing elit, sed do eiusmod tempor incididunt ut labore et dolore magna aliqua.set enim ad minim veniam, quis nostrud exercitation ullamco laboris nisi ut aliquip ex ea commodo consequat. Duis aute irure dolor in reprehenderit in voluptate velit esse cillum dolore eu fugiat nulla pariatur. Excepteur sint occaecat cupidatat non proident, sunt in culpa qui officia deserunt mollit anim id est laborum.Lorem ipsum dolor sit amet, consectetur adipiscing occaecat cupidatat.</p>
<div class="btn" style="left:131px;top:1977px;width:153px">LEARN MORE <span class="go"></span></div>
<div class="shot-frame" style="left:656px;top:1691px"></div>
<div class="shot" style="left:677px;top:1712px;background:linear-gradient(160deg,#dbe7f0 0%,#9fb88a 30%,#4f7a38 55%,#d8473a 75%,#3d7fb8 100%)" role="img" aria-label="Sport shooter with ear protection and red cap aiming a shotgun outdoors"></div>

<!-- ABOUT -->
<section>
  <div class="abs about-band" role="img" aria-label="Two smiling colleagues looking at a laptop together, fading into orange"></div>
  <h2 class="item-title about-title" style="font-size:35px"><span class="marker">ABOUT US</span></h2>
  <p class="copy about-copy">Lorem ipsum dolor sit amet, consectetur adipiscing, sed eiusmod tempor incididunt ut labore et dolore magna aliqua.set enim ad minim veniam, quis nostrud exercitation ullamco laboris nisi ut aliquip commodo consequat. Duis aute irure dolor reprehenderit in voluptate velit esse cillum dolore fugiat nulla pariatur. Excepteur sint occaecat cupidatat non proident, sunt culpa officia deserunt mollit anim id est laborum.Lorem ipsum dolor sit amet, consectetur adipiscing occaecat cupidatat. Lorem ipsum dolor consectetur elit. sed do eiusmod tempor incididunt labore dolore magna aliqua .set enim ad minim veniam, quis nostrud exercitation ullamco.</p>
  <div class="btn dark" style="left:642px;top:2520px;width:152px;height:48px">LEARN MORE <span class="go"></span></div>
</section>

<!-- NEWS -->
<h2 class="section-title" style="top:2711px"><span class="marker">OUR NEWS</span></h2>
<article class="card" style="left:112px">
  <div class="thumb" style="background:linear-gradient(120deg,#6b5a4c 0%,#e6b23c 40%,#8b949e 70%,#d9dadc 100%)" role="img" aria-label="Couple smiling at a laptop on a sofa"></div>
  <div class="date">Apr 16, 2022</div>
  <h3>Lorem ipsum dolor consectetur adipiscing sed eiusmod tempor</h3>
  <p>Lorem ipsum dolor sit consectetur adipiscing consectetur sit adipiscing consectetur dolor sit amet.</p>
  <div class="more">Read More <span class="go"></span></div>
</article>
<article class="card" style="left:446px">
  <div class="thumb" style="background:linear-gradient(180deg,#2f5670 0%,#3d6e8a 45%,#5e5a58 70%,#e9e6e0 100%)" role="img" aria-label="Woman in glasses working at a laptop beside a plant"></div>
  <div class="date">Apr 16, 2022</div>
  <h3>Lorem ipsum dolor consectetur adipiscing sed eiusmod tempor</h3>
  <p>Lorem ipsum dolor sit consectetur adipiscing consectetur sit adipiscing consectetur dolor sit amet.</p>
  <div class="more">Read More <span class="go"></span></div>
</article>
<article class="card" style="left:781px">
  <div class="thumb" style="background:linear-gradient(120deg,#4a3a30 0%,#8a7868 35%,#b9b2a8 60%,#5b5048 100%)" role="img" aria-label="Team gathered around a monitor in a brick-walled office"></div>
  <div class="date">Apr 16, 2022</div>
  <h3>Lorem ipsum dolor consectetur adipiscing sed eiusmod tempor</h3>
  <p>Lorem ipsum dolor sit consectetur adipiscing consectetur sit adipiscing consectetur dolor sit amet.</p>
  <div class="more">Read More <span class="go"></span></div>
</article>

<!-- CONTACT -->
<section>
  <div class="abs contact-left" role="img" aria-label="Support agent with headset, tinted orange"></div>
  <div class="abs contact-right" role="img" aria-label="Faded office team scene in light grey"></div>
  <h2 class="abs contact-title">CONTACT US</h2>
  <div class="contact-row" style="top:3477px"><span class="ico">
    <svg width="18" height="18" viewBox="0 0 24 24"><path fill="none" stroke="#fff" stroke-width="2" d="M6.6 10.8a15 15 0 0 0 6.6 6.6l2.2-2.2a1 1 0 0 1 1-.25 11.4 11.4 0 0 0 3.6.57 1 1 0 0 1 1 1V20a1 1 0 0 1-1 1A17 17 0 0 1 3 4a1 1 0 0 1 1-1h3.5a1 1 0 0 1 1 1c0 1.25.2 2.45.57 3.57a1 1 0 0 1-.25 1z"/></svg></span>+1 555 014 2200</div>
  <div class="contact-row" style="top:3573px"><span class="ico">
    <svg width="18" height="18" viewBox="0 0 24 24"><rect x="3" y="5" width="18" height="14" fill="none" stroke="#fff" stroke-width="2"/><path d="M3 6l9 7 9-7" fill="none" stroke="#fff" stroke-width="2"/></svg></span>info@velora.com</div>
  <div class="contact-row" style="top:3666px"><span class="ico">
    <svg width="18" height="18" viewBox="0 0 24 24"><path fill="#fff" d="M12 2a7 7 0 0 0-7 7c0 5 7 13 7 13s7-8 7-13a7 7 0 0 0-7-7zm0 9.5A2.5 2.5 0 1 1 12 6.5a2.5 2.5 0 0 1 0 5z"/></svg></span>117,Lorem ipsum dolor amet<br>consectetur adipiscing elit.</div>

  <h2 class="item-title touch-title" style="font-size:33px"><span class="marker">GET IN TOUCH</span></h2>
  <div class="field" style="left:686px;top:3432px;width:213px"><svg width="13" height="13" viewBox="0 0 24 24"><circle cx="12" cy="7" r="5" fill="#333"/><path d="M2 23c0-6 4-9 10-9s10 3 10 9z" fill="#333"/></svg>First Name</div>
  <div class="field" style="left:907px;top:3432px;width:214px"><svg width="13" height="13" viewBox="0 0 24 24"><circle cx="12" cy="7" r="5" fill="#333"/><path d="M2 23c0-6 4-9 10-9s10 3 10 9z" fill="#333"/></svg>Last Name</div>
  <div class="field" style="left:686px;top:3489px;width:213px"><svg width="13" height="13" viewBox="0 0 24 24"><rect x="2" y="4" width="20" height="16" fill="#333"/><path d="M2 5l10 8 10-8" fill="none" stroke="#fff" stroke-width="2"/></svg>Email</div>
  <div class="field" style="left:907px;top:3489px;width:214px"><svg width="13" height="13" viewBox="0 0 24 24"><rect x="6" y="1" width="12" height="22" rx="2" fill="none" stroke="#333" stroke-width="2.5"/></svg>Phone</div>
  <div class="field tall" style="left:686px;top:3546px;width:435px"><svg width="14" height="14" viewBox="0 0 24 24"><ellipse cx="12" cy="10" rx="11" ry="8" fill="#333"/><path d="M4 15l-2 6 7-4z" fill="#333"/></svg>Comments</div>
  <div class="btn submit">SUBMIT
    <svg width="16" height="14" viewBox="0 0 24 20"><path fill="#fff" d="M0 8L24 0 18 20 11 13 20 4 8 11z"/></svg></div>
</section>

<!-- FOOTER -->
<footer class="abs footer">
  <div class="brand"><span class="brand-mark"></span>VELORA</div>
  <nav class="foot-nav"><span>Home</span><span>|</span><span>About Us</span><span>|</span><span>Our software</span><span>|</span><span>Our News</span><span>|</span><span>Contact Us</span></nav>
  <div class="foot-social" aria-label="Social links">
    <span><svg width="14" height="14" viewBox="0 0 24 24"><circle cx="12" cy="12" r="9" fill="none" stroke="#fff" stroke-width="2"/><path d="M3 12h18M12 3c4 4 4 14 0 18M12 3c-4 4-4 14 0 18" fill="none" stroke="#fff" stroke-width="1.6"/></svg></span>
    <span><svg width="14" height="14" viewBox="0 0 24 24"><path d="M3 4h18v12H9l-5 4v-4H3z" fill="#fff"/></svg></span>
    <span><svg width="14" height="14" viewBox="0 0 24 24"><circle cx="18" cy="5" r="3" fill="#fff"/><circle cx="6" cy="12" r="3" fill="#fff"/><circle cx="18" cy="19" r="3" fill="#fff"/><path d="M18 5L6 12l12 7" fill="none" stroke="#fff" stroke-width="2"/></svg></span>
    <span><svg width="14" height="14" viewBox="0 0 24 24"><rect x="2" y="5" width="20" height="14" fill="#fff"/><path d="M2 6l10 7 10-7" fill="none" stroke="#f4792b" stroke-width="2"/></svg></span>
  </div>
  <div class="foot-rule"></div>
  <p class="copyright">© 2022 Copyrights velora All Rights Reserved.</p>
</footer>

</body>
</html>
```